Velmora Consulting Business

** Please add the content information from my old business card
1. I would like to see a two sided business card with both options with the 1st Option--Tallow Spire-new WHITE BACKGROUND LOGO
2 nd Option-Tallow Spire - new BLACK- Background Logo
3rd -Option a business card with my Photo on the card
Please add the new word to the card information:
EXECUTION
AS THE OWNER'S REP
WE AIM TO ACHIEVE YOUR
INFRASTRUCTURE VISION with
OUR SPECIALIZATION & EXECUTION in:

FUNDING Planning
BUSINESS Planning
INFRASTRUCTURE Planning
PROJECT Management
Since 2012
_____________________________________________________________________
I want to get spot uv raised printing. I was liking a a nice rich white linen paper stock with black writing & NOT A COLORED CARD other than a variety of white or black cards concept

```html
<!DOCTYPE html>
<html lang="en">
<head>
<meta charset="utf-8">
<title>Velmora Consulting – Business Card</title>
<link href="https://fonts.googleapis.com/css2?family=Open+Sans:wght@400;600;700&display=swap" rel="stylesheet">
<style>
  :root {
    --stage: #e9e6e1;
    --ink: #1f1f21;
    --card-black: #262628;
    --card-white: #f7f7f5;
    --accent: #e31b3b;
    --text-light: #f2f2f2;
    --text-dark: #1c1c1c;
    --brand-faint: #d9d9d9;
  }
  * { box-sizing: border-box; margin: 0; padding: 0; }
  html, body {
    width: 1200px; height: 900px; overflow: hidden;
    background: var(--stage);
    font-family: "Open Sans", Arial, sans-serif;
  }
  .stage { position: relative; width: 1200px; height: 900px; }

  .card {
    position: absolute; width: 600px; height: 343px;
    overflow: hidden;
    box-shadow: 0 10px 28px rgba(0,0,0,.22);
  }

  /* Back side */
  .card--back { left: 100px; top: 80px; background: var(--card-black); color: var(--text-light); }
  .mission {
    position: absolute; left: 70px; top: 150px;
    font-size: 13.5px; line-height: 1.28; letter-spacing: .2px;
    text-transform: uppercase;
  }
  .mission .lower { text-transform: none; }
  .services {
    position: absolute; left: 370px; top: 60px;
    list-style: none; font-size: 12.5px; line-height: 1.35;
  }
  .services li { display: flex; align-items: center; gap: 9px; }
  .services li::before {
    content: ""; width: 7px; height: 7px; background: var(--accent); flex: none;
  }
  .services .since { margin: 6px 0 0 16px; }
  .services .since::before { display: none; }

  .brand { position: absolute; text-align: left; font-weight: 700; }
  .brand__name { display: block; font-size: 44px; line-height: 1; letter-spacing: -.5px; }
  .brand__sub { display: block; font-size: 11px; letter-spacing: 11px; font-weight: 700; margin-top: 6px; }
  .card--back .brand { right: 34px; bottom: 30px; color: var(--text-light); }

  /* Front side */
  .card--front { left: 500px; top: 477px; background: var(--card-white); color: var(--text-dark); }
  .card--front .wave { position: absolute; inset: 0; width: 600px; height: 343px; }
  .card--front .brand { right: 40px; top: 60px; color: var(--brand-faint); }

  .person { position: absolute; left: 46px; top: 88px; }
  .person__name { font-size: 22px; font-weight: 700; }
  .person__title { font-size: 13.5px; color: var(--accent); margin-top: 2px; letter-spacing: .2px; }

  .contacts { position: absolute; left: 46px; top: 168px; list-style: none; font-size: 15px; line-height: 1.55; }
  .contacts li { display: flex; align-items: center; gap: 10px; }
  .contacts svg { width: 15px; height: 15px; flex: none; }

  .locations { position: absolute; left: 46px; top: 262px; font-size: 15px; }
</style>
</head>
<body>
<main class="stage">

  <section class="card card--back" aria-label="Business card, back side">
    <p class="mission">
      Execution<br>
      As the owner's rep<br>
      We aim to achieve your<br>
      Infrastructure vision <span class="lower">with</span><br>
      Our specialization &amp; execution <span class="lower">in:</span>
    </p>
    <ul class="services">
      <li>FUNDING Planning</li>
      <li>BUSINESS Planning</li>
      <li>INFRASTRUCTURE Planning</li>
      <li>PROJECT Management</li>
      <li class="since">Since 2012</li>
    </ul>
    <div class="brand">
      <span class="brand__name">Velmora</span>
      <span class="brand__sub">CONSULTING</span>
    </div>
  </section>

  <section class="card card--front" aria-label="Business card, front side">
    <svg class="wave" viewBox="0 0 600 343" aria-hidden="true">
      <path d="M0,343 L0,322 C220,330 430,255 600,140 L600,343 Z" fill="var(--ink)"/>
      <path d="M0,300 C200,312 360,268 470,205 C360,276 210,322 0,318 Z" fill="var(--accent)"/>
    </svg>

    <div class="brand">
      <span class="brand__name">Velmora</span>
      <span class="brand__sub">CONSULTING</span>
    </div>

    <div class="person">
      <h1 class="person__name">Corinne Ashdale-Varma</h1>
      <p class="person__title">CEO / LEAD PROJECT MANAGER</p>
    </div>

    <ul class="contacts">
      <li>
        <svg viewBox="0 0 16 16" aria-hidden="true"><path d="M4 1l3 3-2 2c1 2 3 4 5 5l2-2 3 3-2 3C7 15 1 9 1 3z" fill="var(--accent)"/></svg>
        867 555.0142
      </li>
      <li>
        <svg viewBox="0 0 16 16" aria-hidden="true"><rect x="1" y="3" width="14" height="10" fill="var(--accent)"/><path d="M1 3l7 6 7-6" stroke="#fff" stroke-width="1.3" fill="none"/></svg>
        corinne@velmora.ca
      </li>
      <li>
        <svg viewBox="0 0 16 16" aria-hidden="true"><circle cx="8" cy="8" r="6.5" fill="none" stroke="var(--accent)" stroke-width="1.6"/><path d="M1.5 8h13M8 1.5v13M3 4.5h10M3 11.5h10" stroke="var(--accent)" stroke-width="1.1"/><ellipse cx="8" cy="8" rx="3" ry="6.5" fill="none" stroke="var(--accent)" stroke-width="1.1"/></svg>
        www.velmora.ca
      </li>
    </ul>

    <p class="locations">Iqaluit NU &bull; Halifax NS</p>
  </section>

</main>
</body>
</html>
```